3 Page Design for Ninth Bay Capital

We want a Home Page, About Page, and Products & Services Page for Ninth Bay Capital. Please refer to the attached docs for more info.
If done in Figma, would like Figma files that can easily be ported to Wordpress.

```html
<!DOCTYPE html>
<html lang="en">
<head>
<meta charset="utf-8">
<title>Ninth Bay Capital – Home</title>
<link href="https://fonts.googleapis.com/css2?family=Arimo:wght@400;700&display=swap" rel="stylesheet">
<style>
:root{
  --red:#9b1b30;
  --tan:#e8dac5;
  --tan-icon:#e6d6c0;
  --brown:#8a704e;
  --dark:#2d2d2d;
  --text:#333333;
  --muted:#666666;
  --white:#ffffff;
}
*{margin:0;padding:0;box-sizing:border-box}
html,body{width:1200px;height:2721px;overflow:hidden;background:var(--white)}
body{font-family:"Arimo",Helvetica,Arial,sans-serif;color:var(--text);position:relative}
.abs{position:absolute}
.btn{position:absolute;display:flex;align-items:center;justify-content:center;background:var(--red);color:var(--white);font-size:13px;text-transform:uppercase;border-radius:3px;letter-spacing:-.1px}
/* header */
.site-header{position:absolute;left:0;top:0;width:1200px;height:120px;background:var(--white);border-bottom:1px solid #e3e3e3}
.brand{position:absolute;left:111px;top:30px;display:flex;align-items:center;gap:10px}
.brand-dot{width:46px;height:46px;border-radius:50%;background:var(--brown)}
.brand-name{font-weight:700;font-size:17px;color:var(--dark)}
.main-nav{position:absolute;top:83px;right:112px;display:flex;gap:43px;font-size:16px;color:#777}
.main-nav .active{color:#111}
/* hero */
.hero{position:absolute;left:0;top:120px;width:1200px;height:590px}
.hero-photo{position:absolute;inset:0;background:linear-gradient(90deg,#3d3732 0%,#7b736c 30%,#b9b3ad 55%,#c7c2bd 62%,#d33f72 68%,#d94a7b 82%,#cfcac6 100%)}
.hero-photo::after{content:"";position:absolute;inset:0;background:linear-gradient(180deg,rgba(0,0,0,0) 60%,rgba(80,60,40,.35) 100%)}
.hero h1{position:absolute;left:111px;top:128px;color:var(--white);font-size:55px;line-height:68px;font-weight:700}
.hero h1 span{display:block;font-weight:400}
.hero p{position:absolute;left:111px;top:272px;width:560px;color:var(--white);font-size:15px;line-height:23px}
.hero-emblem{position:absolute;left:560px;top:667px;width:80px;height:80px;border-radius:50%;background:var(--white);box-shadow:0 2px 8px rgba(0,0,0,.25);display:flex;align-items:center;justify-content:center;font-size:11px;font-weight:700;color:var(--dark);text-align:center;line-height:13px}
/* services */
.section-title{position:absolute;left:0;width:1200px;text-align:center;font-size:40px;font-weight:400;color:var(--text)}
.section-title b{font-weight:700}
.service-label{position:absolute;width:220px;text-align:center;font-size:17px;color:#111}
.service-icon{position:absolute;width:152px;height:152px;border-radius:50%;background:var(--tan-icon)}
/* planning */
.planning{position:absolute;left:0;top:1237px;width:1200px;height:545px}
.planning-photo{position:absolute;inset:0;background:linear-gradient(90deg,#e2d6c3 0%,#e9dfcf 35%,#e3d6c2 60%,#e5d8c4 100%)}
.planning h2{position:absolute;left:111px;top:80px;font-size:38px;line-height:47px;color:var(--dark);font-weight:700}
.planning h2 span{display:block;font-weight:400}
.planning .copy{position:absolute;left:111px;top:200px;width:570px;font-size:15px;line-height:25.6px;color:#3a3a3a}
.checks{position:absolute;left:111px;top:315px;list-style:none;font-size:15px;color:#3a3a3a}
.checks li{height:31px;display:flex;align-items:center;gap:14px}
.watermark{position:absolute;left:748px;top:103px;width:318px;height:318px;border-radius:50%;background:rgba(255,255,255,.55);display:flex;align-items:center;justify-content:center;font-size:34px;font-weight:700;color:var(--white)}
/* mission */
.mission-copy{position:absolute;left:150px;top:1928px;width:900px;text-align:center;font-size:15px;line-height:24px;color:#444}
/* cta */
.cta{position:absolute;left:111px;top:2101px;width:977px;height:226px;background:var(--tan);border-radius:4px}
.cta h2{position:absolute;left:44px;top:38px;font-size:38px;line-height:47px;color:var(--dark);font-weight:700}
.cta h2 span{display:block;font-weight:400}
.cta p{position:absolute;left:44px;top:140px;width:640px;font-size:15px;line-height:26px;color:#777}
/* footer */
.site-footer{position:absolute;left:0;top:2400px;width:1200px;height:321px}
.footer-name{position:absolute;left:0;top:130px;width:1200px;text-align:center;color:var(--white);font-weight:700;font-size:24px}
.footer-dot{position:absolute;left:576px;top:70px;width:48px;height:48px;border-radius:50%;background:var(--white)}
.footer-nav{position:absolute;left:0;top:234px;width:1200px;display:flex;justify-content:center;gap:43px;color:var(--white);font-size:16px;text-transform:uppercase}
.footer-rule{position:absolute;left:111px;top:268px;width:977px;height:1px;background:#888}
.copyright{position:absolute;left:0;top:281px;width:1200px;text-align:center;color:var(--white);font-size:11px}
</style>
</head>
<body>

<header class="site-header">
  <div class="brand"><span class="brand-dot"></span><span class="brand-name">NINTH BAY CAPITAL</span></div>
  <a class="btn" style="left:859px;top:23px;width:229px;height:36px">Schedule a Consultation →</a>
  <nav class="main-nav"><span class="active">HOME</span><span>ABOUT US</span><span>PRODUCTS &amp; SERVICES</span><span>CONTACT US</span></nav>
</header>

<section class="hero">
  <div class="hero-photo" role="img" aria-label="Smiling woman jogging on a bridge with earphones"></div>
  <svg class="abs" style="left:0;top:0" width="1200" height="590" viewBox="0 0 1200 590">
    <polygon points="0,471 600,584 1200,471 1200,590 0,590" fill="var(--brown)"/>
    <polygon points="0,522 600,590 1200,522 1200,590 0,590" fill="var(--white)"/>
  </svg>
  <h1>Own Your Future.<span>Win the Ninth Bay.</span></h1>
  <p>Where strategic planning, disciplined investing, and comprehensive guidance come together to help you build long-term financial confidence.</p>
  <a class="btn" style="left:111px;top:337px;width:173px;height:36px">Start Your Plan →</a>
</section>
<div class="hero-emblem">Ninth<br>Bay</div>

<h2 class="section-title" style="top:826px"><b>A Smarter Way</b> to Build Wealth</h2>

<svg class="abs" style="left:0;top:930px" width="1200" height="230" viewBox="0 0 1200 230">
  <g fill="none" stroke="#999" stroke-width="1" stroke-dasharray="4 4">
    <path d="M110,112 A98,98 0 0 1 306,112"/>
    <path d="M306,112 A98,98 0 0 0 502,112"/>
    <path d="M502,112 A98,98 0 0 1 697,112"/>
    <path d="M697,112 A98,98 0 0 0 893,112"/>
    <path d="M893,112 A98,98 0 0 1 1088,112"/>
  </g>
</svg>
<div class="service-icon" style="left:132px;top:966px"></div>
<div class="service-icon" style="left:327px;top:966px"></div>
<div class="service-icon" style="left:523px;top:966px"></div>
<div class="service-icon" style="left:718px;top:966px"></div>
<div class="service-icon" style="left:914px;top:966px"></div>
<svg class="abs" style="left:0;top:990px" width="1200" height="110" viewBox="0 0 1200 110" fill="#555">
  <circle cx="222" cy="38" r="18"/><path d="M172,70 l20,-14 h30 l20,-8 v12 l-28,16 h-34z"/>
  <rect x="368" y="60" width="8" height="30"/><rect x="380" y="44" width="8" height="46"/><polygon points="392,90 392,40 384,40 399,22 414,40 406,40 406,90"/><circle cx="422" cy="62" r="18"/>
  <circle cx="594" cy="32" r="16"/><path d="M574,80 h48 M580,60 v20 M612,50 v30" stroke="#555" stroke-width="5" fill="none"/>
  <path d="M762,16 l32,12 v24 c0,20 -14,34 -32,42 c-18,-8 -32,-22 -32,-42 v-24z"/><path d="M750,52 l10,10 l18,-18" stroke="var(--tan-icon)" stroke-width="6" fill="none"/>
  <rect x="978" y="36" width="6" height="20"/><rect x="990" y="28" width="6" height="28"/><rect x="1002" y="20" width="6" height="36"/><rect x="1014" y="12" width="6" height="44"/><circle cx="990" cy="70" r="20"/><circle cx="966" cy="42" r="8"/>
</svg>
<div class="service-label" style="left:293px;top:931px">Investment Management</div>
<div class="service-label" style="left:688px;top:931px">Insurance &amp; Protection</div>
<div class="service-label" style="left:96px;top:1134px">Financial Planning</div>
<div class="service-label" style="left:491px;top:1134px">Retirement Planning</div>
<div class="service-label" style="left:879px;top:1134px">Business Solutions</div>

<section class="planning">
  <div class="planning-photo" role="img" aria-label="Faded photo of a woman working at a desk with sticky notes on a wall"></div>
  <h2>Planning for the Life<span>Beyond the Clock</span></h2>
  <p class="copy">Just like great athletes prepare for the moments beyond regulation play, true financial confidence comes from preparation for the unexpected. The Ninth Bay represents the extra effort, the deeper strategy, and the long view that sets you up for enduring success.</p>
  <ul class="checks">
    <li><span>»</span>The decisions you make today.</li>
    <li><span>»</span>The outcomes they create tomorrow.</li>
    <li><span>»</span>The legacy they build over time.</li>
  </ul>
  <a class="btn" style="left:111px;top:419px;width:131px;height:36px">Read More →</a>
  <div class="watermark">Ninth Bay</div>
</section>

<h2 class="section-title" style="top:1858px"><b>Our</b> Mission</h2>
<p class="mission-copy">Lorem ipsum dolor sit amet, consectetur adipiscing elit, sed do eiusmod tempor incididunt<br>ut labore et dolore magna aliqua. Ut enim ad minim veniam, quis nostrud exercitation ullamco laboris nisi ut aliquip ex ea<br>commodo consequat. Duis aute irure dolor in reprehenderit in voluptate velit esse cillum dolore eu fugiat nulla pariatur.<br>Excepteur sint occaecat cupidatat non proident, sunt in culpa qui officia deserunt mollit anim id est laborum.</p>

<section class="cta">
  <h2>Let’s Build<span>Your Ninth Bay Strategy</span></h2>
  <p>Your financial future deserves clarity, structure, and a long-term plan you can trust. Start the conversation—no pressure, just guidance.</p>
  <a class="btn" style="left:703px;top:96px;width:231px;height:36px">Schedule a Consultation →</a>
</section>

<footer class="site-footer">
  <svg class="abs" style="left:0;top:0" width="1200" height="321" viewBox="0 0 1200 321">
    <polygon points="0,75 610,13 1200,75 1200,321 0,321" fill="var(--brown)"/>
    <polygon points="0,130 610,13 1200,130 1200,321 0,321" fill="var(--dark)"/>
  </svg>
  <div class="footer-dot"></div>
  <div class="footer-name">NINTH BAY CAPITAL</div>
  <nav class="footer-nav"><span>Home</span><span>About Us</span><span>Products &amp; Services</span><span>Contact Us</span></nav>
  <div class="footer-rule"></div>
  <div class="copyright">COPYRIGHT © 2025 NINTH BAY CAPITAL. ALL RIGHTS RESERVED.</div>
</footer>

</body>
</html>
```